New Australian Event targeting the Office Industry Web Design Project

Deskora* is an exhibition and conference aimed at meeting the business needs of office professionals – the visitors are the ones that make purchase decisions when buying anything to do with the office from office equipment and stationery, event management, training and travel.

The range of exhibitors at this show is unique in Aust – therefore no other show that is similar or as relevant for this target market.
Being that it is a new show – visitors and exhibitors will want a better understanding of what the show is about, and how it is beneficial to them.

Deskora UK, Canada & US – will need to keep similar ‘brand guidelines’ but the functionality and layout is not appropriate. Eg. half a page on static banner branding is waste of space.
http://www.deskorashow.co.uk/ and www.deskoracanada.ca and http://www.deskora-tradeshow.com/

Some examples of Aus websites who are targeting same type of customer:
http://www.workwrens.com.au/
http://www.tolvex.com.au/
http://www.quenlaproducts.com.au/quenla/en_au/
Updates

Hi All, 

Thanks for the interest in our competition, I will be away until the 11th of January at which point i will comment on the designs. 

Thanks and Merry Xmas. 

Target Market(s)

Office Managers, Executive Assistants / Personal Assistants, Office Professionals,

Industry/Entity Type

Training

Requirements
Must have
• The website will be built into a CMS. The website will need to offer:

Homepage:
Clear CTA's - Visitor (Register free) and Exhibitor (Book a Stand)
“what’s new/hot” section on homepage
3 or 4 content areas for in-event promotions
Data capture – this will need to very visible on home page
All to fit within 'one fold'.

Content Page:
Relevant CTA's - Visitor (Register free) and Exhibitor (Book a Stand)

Sitewide:
Social media integration

I would like to see designs for a content page as well as the homepage.
Nice to have
• Floating navigation/call to action bar (top, bottom or side) - eg, http://brightwirenews.com/me/2011/12/20/sample-article-about-regional-news-story/, http://pixelhive.com/2011/12/19/snapfolio-2011/
Should not have
• Elements requiring Vortiq

```html
<!DOCTYPE html>
<html lang="en">
<head>
<meta charset="utf-8">
<title>Deskora Melbourne 2012</title>
<link rel="stylesheet" href="https://fonts.googleapis.com/css2?family=Arvo:wght@700&family=Arimo:wght@400;700&display=swap">
<style>
  :root {
    --orange: #f7941d;
    --orange-dark: #c66f12;
    --ink: #0d0d0d;
    --panel: #111111;
    --body-text: #8a8a8a;
    --lead-text: #a8a8a8;
    --white: #ffffff;
    --footer-ink: #1a1a1a;
  }
  * { box-sizing: border-box; margin: 0; padding: 0; }
  html, body { width: 1200px; height: 960px; overflow: hidden; background: var(--white); }
  .page { position: relative; width: 1200px; height: 960px; overflow: hidden; font-family: "Arimo", Arial, sans-serif; }
  .backdrop { position: absolute; inset: 0; }

  .brand { position: absolute; left: 78px; top: 48px; }
  .brand-name { display: flex; align-items: center; gap: 14px; font-weight: 700; font-size: 62px; color: var(--ink); line-height: 1; }
  .brand-square { width: 22px; height: 22px; background: var(--orange); }
  .brand-meta { margin-top: 10px; font-size: 17px; font-weight: 700; color: var(--ink); white-space: nowrap; }
  .brand-meta .date { color: var(--orange); }

  .cta { position: absolute; font-family: "Arvo", Georgia, serif; font-weight: 700; color: var(--white); font-size: 16px; line-height: 19px; text-align: center; white-space: nowrap; }
  .cta-visitor { left: 640px; top: 26px; width: 130px; }
  .cta-exhibitor { left: 570px; top: 108px; width: 145px; }
  .cta-arrow { position: absolute; }

  .newsletter { position: absolute; left: 826px; top: 35px; display: flex; align-items: center; gap: 14px; }
  .newsletter label { color: var(--white); font-size: 12px; font-weight: 700; white-space: nowrap; }
  .newsletter input { width: 157px; height: 22px; border: 1px solid #ccc; font: 12px "Arimo", Arial, sans-serif; color: #333; text-align: center; background: var(--white); }

  .intro { position: absolute; left: 540px; top: 176px; width: 614px; }
  .intro h1 { font-weight: 400; font-size: 22px; line-height: 26px; color: var(--lead-text); margin-bottom: 20px; }
  .intro h1 em { font-style: normal; color: var(--orange); }
  .intro p { font-size: 11.6px; line-height: 24.5px; color: var(--body-text); }
  .intro p + p { margin-top: 24px; }
  .hl { color: var(--orange); }
  .more { color: var(--orange); font-style: italic; }

  .main-nav { position: absolute; left: 45px; top: 264px; }
  .nav-item { position: relative; height: 63px; margin-bottom: 10px; }
  .nav-side { position: absolute; left: 0; top: 0; }
  .nav-label { position: absolute; left: 53px; top: 0; height: 63px; display: flex; align-items: center; padding-left: 10px; background: var(--orange); font-family: "Arvo", Georgia, serif; font-weight: 700; font-size: 20px; color: var(--ink); white-space: nowrap; }

  .promo { position: absolute; border: 3px solid var(--white); }
  .promo-a { left: 620px; top: 742px; width: 148px; height: 161px; background: linear-gradient(180deg, #c97b8a 0%, #3d3035 45%, #b0306a 100%); }
  .promo-b { left: 800px; top: 742px; width: 148px; height: 161px; background: linear-gradient(180deg, #c97b8a 0%, #3d3035 45%, #b0306a 100%); }
  .promo-c { left: 980px; top: 723px; width: 180px; height: 188px; background: linear-gradient(180deg, #3a2f2f 0%, #6b4a4f 50%, #c0306e 100%); }

  .social { position: absolute; top: 853px; left: 20px; display: flex; gap: 30px; }
  .social a { display: flex; align-items: center; gap: 10px; text-decoration: none; font-family: "Arvo", Georgia, serif; font-weight: 700; font-size: 15px; color: var(--footer-ink); white-space: nowrap; }
  .social .dot { width: 52px; height: 52px; border-radius: 50%; background: #2a2a2a; }
  .copyright { position: absolute; left: 22px; top: 933px; display: flex; align-items: center; gap: 8px; font-size: 10.5px; color: var(--footer-ink); }
  .copyright .dot { width: 16px; height: 16px; border-radius: 50%; border: 2px solid var(--footer-ink); }
</style>
</head>
<body>
<div class="page">
  <svg class="backdrop" width="1200" height="960" viewBox="0 0 1200 960" aria-hidden="true">
    <defs>
      <linearGradient id="footerBand" x1="0" y1="0" x2="0" y2="1">
        <stop offset="0" stop-color="#5c5c5c" stop-opacity="0.8"/>
        <stop offset="1" stop-color="#6e6e6e" stop-opacity="0.9"/>
      </linearGradient>
    </defs>
    <path d="M600 0 C 480 110 432 300 432 520 L432 960 L1200 960 L1200 0 Z" fill="var(--panel)"/>
    <rect x="0" y="810" width="1200" height="150" fill="url(#footerBand)"/>
  </svg>

  <header class="brand">
    <div class="brand-name"><span>Deskora</span><span class="brand-square"></span></div>
    <div class="brand-meta">MELBOURNE <span class="date">May 22-23 2012</span></div>
    <div class="brand-meta">Harbourside Exhibition Centre | Australia</div>
  </header>

  <svg class="cta-arrow" style="left:552px;top:8px" width="80" height="72" viewBox="0 0 80 72" aria-hidden="true">
    <polygon points="0,18 42,18 42,0 80,36 42,72 42,54 0,54" fill="var(--orange)"/>
  </svg>
  <svg class="cta-arrow" style="left:470px;top:90px" width="80" height="72" viewBox="0 0 80 72" aria-hidden="true">
    <polygon points="0,18 42,18 42,0 80,36 42,72 42,54 0,54" fill="var(--orange)"/>
  </svg>
  <a class="cta cta-visitor">Visitor:<br>Register Free</a>
  <a class="cta cta-exhibitor">Exhbitor:<br>Book a Stand</a>

  <form class="newsletter">
    <label for="email">Subscribe to our newsletter:</label>
    <input id="email" type="text" value="email@example.com">
  </form>

  <section class="intro">
    <h1>The <em>essential</em> event for career focused <em>PAs, EAs &amp; Office Managers</em>.</h1>
    <p>Fresh from the success of our second fantastic show which saw the launch of <span class="hl">Desk Pro Day</span>, the first ever online portal for Office Managers, OFPRO.co.uk as well as many other new and innovative products and services all aimed at enabling todays office professional to excel in their increasingly demanding job roles.</p>
    <p>Deskora 2011 saw <span class="hl">visitor numbers increase by 18% and exhibitors by 26%</span> – the feedback so far is brilliant from both sides with an incredible 60% of exhibitors rebooking onsite!<br>
    Please browse this website to see what was on offer this year as we update the site ready for an even bigger and better show for 2012 – having already outgrown our venue we move to Grand Hall, Westbury next year so keep an eye out for the latest developments as they happen. <span class="more">Read more…</span><br>
    Mark your diary for <span class="hl">Wednesday 12th and Thursday 13th of September 2012!</span></p>
    <p>1st annual Desk Pro Survey results announced - UK Survey reveals feelings of the nation’s PAs<br>
    To coincide with the launch of the UK’s first ever Desk Pro Day, event organisers Brightline Business Communications UK have released a summary of the UK’s 1st annual Desk Pro Survey results. Introduced to discover more about the feelings and aspirations of the UK’s <span class="hl">estimated 600,000 personal assistants and executive assistants</span>, the 1st annual Desk Pro Survey – one of the most comprehensive surveys of Britain’s PAs ever undertaken – was completed by 1,637 respondents during the last week of August 2011 (Friday 26 August and Thursday 1 September).</p>
  </section>

  <nav class="main-nav">
    <div class="nav-item"><svg class="nav-side" width="56" height="63" aria-hidden="true"><polygon points="0,6 55,0 55,63 0,50" fill="var(--orange-dark)"/></svg><a class="nav-label" style="width:229px">About the Show</a></div>
    <div class="nav-item"><svg class="nav-side" width="56" height="63" aria-hidden="true"><polygon points="0,6 55,0 55,63 0,50" fill="var(--orange-dark)"/></svg><a class="nav-label" style="width:155px">Whats on</a></div>
    <div class="nav-item"><svg class="nav-side" width="56" height="63" aria-hidden="true"><polygon points="0,6 55,0 55,63 0,50" fill="var(--orange-dark)"/></svg><a class="nav-label" style="width:145px">Register</a></div>
    <div class="nav-item"><svg class="nav-side" width="56" height="63" aria-hidden="true"><polygon points="0,6 55,0 55,63 0,50" fill="var(--orange-dark)"/></svg><a class="nav-label" style="width:249px">How to Exhibit</a></div>
    <div class="nav-item"><svg class="nav-side" width="56" height="63" aria-hidden="true"><polygon points="0,6 55,0 55,63 0,50" fill="var(--orange-dark)"/></svg><a class="nav-label" style="width:80px">Blog</a></div>
    <div class="nav-item"><svg class="nav-side" width="56" height="63" aria-hidden="true"><polygon points="0,6 55,0 55,63 0,50" fill="var(--orange-dark)"/></svg><a class="nav-label" style="width:170px">Contact Us</a></div>
  </nav>

  <div class="promo promo-a" role="img" aria-label="Photo of visitors at an exhibition stand with a striped awning"></div>
  <div class="promo promo-b" role="img" aria-label="Photo of visitors at an exhibition stand with a striped awning"></div>
  <div class="promo promo-c" role="img" aria-label="Photo of a busy exhibition hall crowd"></div>

  <footer>
    <div class="social">
      <a><span class="dot"></span>Like us</a>
      <a><span class="dot"></span>Follow us</a>
      <a><span class="dot"></span>RSS Feed</a>
    </div>
    <div class="copyright"><span class="dot"></span>Copyright 2012 Deskora Australia</div>
  </footer>
</div>
</body>
</html>
```